Harbor Crestline (Business Card Design)

Need business cards designed. Something modern, chic, and sleek. Mabye the back of the card should be the navy blue that is in the logo and then just the logo on the back.

Target Market(s)

Those in the hotel, office, and renovation industry

Contact Information for Business Card

1. Logo 2. Dorian Fenwick 3. CEO/Founder 4. Phone: (833) HarbCre / (833) 427-2731 5. Email: dorian@theharborcrestline.com 6. Website: www.theharborcrestline.com

Font styles to use
Other font styles liked:
• Look at the logo font and base the font for everything else off of that.

Colors
0054AA
0677BA
7BADD7
CADEEF
E8F1F8

Requirements
Must have
• Colors that are associated in the logo
Nice to have
• Sleek modern clean and chic design.

```html
<!DOCTYPE html>
<html lang="en">
<head>
<meta charset="utf-8">
<title>Harbor Crestline — Business Card</title>
<link rel="stylesheet" href="https://fonts.googleapis.com/css2?family=Montserrat:wght@400;600;700&family=Poppins:wght@400;500&display=swap">
<style>
  :root {
    --navy: #0c1a4d;
    --navy-deep: #091540;
    --navy-soft: #13286b;
    --gold: #c9a24a;
    --white: #ffffff;
    --ink: #141a33;
    --rule: #c9ccd6;
    --backdrop: #2b2b2e;
  }
  * { box-sizing: border-box; margin: 0; padding: 0; }
  html, body {
    width: 1200px; height: 689px; overflow: hidden;
    background: var(--backdrop);
  }
  .sheet {
    width: 1200px; height: 689px;
    display: flex; align-items: center; justify-content: center; gap: 40px;
  }
  .card {
    position: relative;
    width: 540px; height: 309px;
    border-radius: 18px;
    overflow: hidden;
  }

  /* Back of card */
  .card-back {
    background: var(--navy);
    display: flex; align-items: center; justify-content: center;
  }
  .card-back .tonal-field {
    position: absolute; inset: 0;
    background: radial-gradient(ellipse at 70% 30%, var(--navy-soft) 0%, var(--navy) 55%, var(--navy-deep) 100%);
  }
  .card-back .brand {
    position: relative;
    display: flex; align-items: center; gap: 14px;
  }
  .brand-square {
    width: 14px; height: 14px; background: var(--gold);
  }
  .brand-name {
    font-family: "Montserrat", sans-serif;
    font-weight: 600;
    letter-spacing: 0.14em;
    text-transform: uppercase;
    line-height: 1.1;
  }
  .card-back .brand-name { color: var(--white); font-size: 30px; }

  /* Front of card */
  .card-front { background: var(--white); }
  .card-front .identity {
    position: absolute; left: 34px; top: 0; width: 196px; height: 240px;
    display: flex; align-items: center; gap: 12px;
  }
  .card-front .brand-name { color: var(--navy); font-size: 22px; }
  .card-front .divider {
    position: absolute; left: 248px; top: 34px;
    width: 1px; height: 176px; background: var(--rule);
  }
  .card-front .details {
    position: absolute; left: 272px; top: 42px; right: 20px;
  }
  .person-name {
    font-family: "Montserrat", sans-serif;
    font-weight: 700; font-size: 21px;
    color: var(--navy); text-transform: uppercase; letter-spacing: 0.02em;
  }
  .person-role {
    font-family: "Montserrat", sans-serif;
    font-weight: 400; font-size: 12px;
    color: var(--gold); text-transform: uppercase; letter-spacing: 0.04em;
    margin-top: 2px;
  }
  .contact-list { list-style: none; margin-top: 28px; }
  .contact-item {
    display: flex; align-items: center; gap: 8px;
    font-family: "Poppins", sans-serif; font-size: 11.5px; color: var(--ink);
    margin-bottom: 9px; white-space: nowrap;
  }
  .contact-icon { width: 13px; height: 13px; flex: none; color: var(--navy); }
  .card-front .band-accent {
    position: absolute; left: 0; right: 0; bottom: 56px; height: 4px;
    background: var(--gold);
  }
  .card-front .band {
    position: absolute; left: 0; right: 0; bottom: 0; height: 56px;
    background: var(--navy);
  }
</style>
</head>
<body>
<main class="sheet">
  <section class="card card-back" aria-label="Card back">
    <div class="tonal-field" role="img" aria-label="Navy field with a tonal embossed pattern"></div>
    <div class="brand">
      <span class="brand-square"></span>
      <span class="brand-name">Harbor<br>Crestline</span>
    </div>
  </section>

  <section class="card card-front" aria-label="Card front">
    <div class="identity">
      <span class="brand-square"></span>
      <span class="brand-name">Harbor<br>Crestline</span>
    </div>
    <div class="divider"></div>
    <div class="details">
      <h1 class="person-name">Dorian Fenwick</h1>
      <p class="person-role">CEO/Founder</p>
      <ul class="contact-list">
        <li class="contact-item">
          <svg class="contact-icon" viewBox="0 0 24 24" aria-hidden="true"><path fill="currentColor" d="M6.6 10.8a15.1 15.1 0 0 0 6.6 6.6l2.2-2.2a1 1 0 0 1 1-.25 11.4 11.4 0 0 0 3.6.6 1 1 0 0 1 1 1V20a1 1 0 0 1-1 1A17 17 0 0 1 3 4a1 1 0 0 1 1-1h3.5a1 1 0 0 1 1 1c0 1.25.2 2.45.6 3.6a1 1 0 0 1-.25 1z"/></svg>
          (833) HarbCre / (833) 427-2731
        </li>
        <li class="contact-item">
          <svg class="contact-icon" viewBox="0 0 24 24" aria-hidden="true"><path fill="currentColor" d="M2 5h20v14H2zm2 2v.5l8 5 8-5V7l-8 5z"/></svg>
          dorian@theharborcrestline.com
        </li>
        <li class="contact-item">
          <svg class="contact-icon" viewBox="0 0 24 24" aria-hidden="true"><g fill="none" stroke="currentColor" stroke-width="2"><circle cx="12" cy="12" r="9"/><ellipse cx="12" cy="12" rx="4" ry="9"/><path d="M3 12h18M5 7h14M5 17h14"/></g></svg>
          www.theharborcrestline.com
        </li>
      </ul>
    </div>
    <div class="band-accent"></div>
    <div class="band"></div>
  </section>
</main>
</body>
</html>
```